Business Card Design Project

Business Card
We are rebranding with a new logo
Industry/Entity Type
Business
Contact Information for Business Card
Dennis Morvale +61 487215963 dennis@quorv.com.au P.O. Box 872 Fernlow QLD 4309
Requirements
Must have
- Logo

```html
<!DOCTYPE html>
<html lang="en">
<head>
<meta charset="UTF-8">
<title>Quorv International – Business Card</title>
<link rel="stylesheet" href="https://fonts.googleapis.com/css2?family=Play:wght@400;700&display=swap">
<style>
  :root {
    --backdrop: #e4e4e4;
    --card: #ffffff;
    --brand-blue: #1a8ac6;
    --accent-orange: #f08a24;
    --text-grey: #7b7b7b;
  }
  html, body {
    margin: 0;
    padding: 0;
    width: 1200px;
    height: 1000px;
    overflow: hidden;
    background: var(--backdrop);
    font-family: "Play", sans-serif;
  }
  .business-card {
    position: absolute;
    left: 221px;
    top: 277px;
    width: 760px;
    height: 432px;
    background: var(--card);
  }
  .brand-name {
    position: absolute;
    right: 414px;
    top: 175px;
    margin: 0;
    font-size: 21px;
    font-weight: 700;
    color: var(--brand-blue);
    white-space: nowrap;
    letter-spacing: 0.5px;
  }
  .divider {
    position: absolute;
    left: 388px;
    top: 162px;
    width: 2px;
    height: 110px;
    background: var(--brand-blue);
  }
  .person-name {
    position: absolute;
    left: 431px;
    top: 161px;
    margin: 0;
    font-size: 21px;
    font-weight: 400;
    color: var(--brand-blue);
    text-transform: uppercase;
    letter-spacing: 0.5px;
  }
  .contact-list {
    position: absolute;
    left: 432px;
    top: 226px;
    margin: 0;
    padding: 0;
    list-style: none;
  }
  .contact-item {
    display: flex;
    align-items: center;
    height: 24px;
    font-size: 16px;
    color: var(--text-grey);
    letter-spacing: 0.3px;
  }
  .contact-icon {
    width: 14px;
    height: 14px;
    margin-right: 18px;
    fill: var(--accent-orange);
    flex-shrink: 0;
  }
  .postal-address {
    position: absolute;
    left: 0;
    right: 0;
    top: 375px;
    margin: 0;
    text-align: center;
    font-size: 16px;
    color: var(--text-grey);
    letter-spacing: 0.3px;
  }
</style>
</head>
<body>
  <div class="business-card">
    <p class="brand-name">Quorv International</p>
    <div class="divider"></div>
    <h1 class="person-name">Dennis Morvale</h1>
    <ul class="contact-list">
      <li class="contact-item">
        <svg class="contact-icon" viewBox="0 0 14 14" aria-hidden="true">
          <path d="M3.5 0h7a1.5 1.5 0 0 1 1.5 1.5v11a1.5 1.5 0 0 1-1.5 1.5h-7A1.5 1.5 0 0 1 2 12.5v-11A1.5 1.5 0 0 1 3.5 0zm0.3 1.6v9.6h6.4V1.6z"/>
        </svg>
        +61 487215963
      </li>
      <li class="contact-item">
        <svg class="contact-icon" viewBox="0 0 14 14" aria-hidden="true">
          <path d="M0 3h14v1L7 8 0 4z"/>
          <path d="M0 5.5l7 4 7-4V12H0z"/>
        </svg>
        dennis@quorv.com.au
      </li>
    </ul>
    <p class="postal-address">P.O. Box 872 Fernlow QLD 4309</p>
  </div>
</body>
</html>
```